Upmarket Dessert Lounge needs a Business Card Design

We are an upmarket dessert lounge needing a business card to match our image.

We want something that is simple yet beautiful, feminine, classy, sophisticated and elegant. We want it to stand out and don't mind if it is bold.

The design should include our logo and colours of red or maroon with gold highlights. We don't mind if black is used.

Marlow & Quince

Target Market(s)

For those who like to indulge or treat themselves and give in to their temptations on good quality desserts.

Industry/Entity Type

Business

Requirements
Must have
• Must include our logo and our name

Marlow & Quince

M & Q

```html
<!DOCTYPE html>
<html lang="en">
<head>
<meta charset="utf-8">
<title>Marlow &amp; Quince — Business Card</title>
<link href="https://fonts.googleapis.com/css2?family=Cinzel:wght@600&family=Libre+Baskerville:wght@700&family=Arimo:wght@400&display=swap" rel="stylesheet">
<style>
  :root {
    --canvas: #ecebe8;
    --maroon: #8a1a20;
    --maroon-deep: #5e0e13;
    --maroon-light: #a3262c;
    --gold: #e3b47a;
    --gold-soft: #f3cf9c;
    --cream: #fbf6ef;
    --ink: #2a2424;
    --white: #ffffff;
  }
  * { box-sizing: border-box; margin: 0; padding: 0; }
  html, body { width: 1200px; height: 951px; overflow: hidden; }
  body { background: var(--canvas); position: relative; font-family: "Arimo", Arial, sans-serif; }

  .card {
    position: absolute;
    width: 620px;
    height: 354px;
    border-radius: 22px;
    overflow: hidden;
    box-shadow: 0 10px 28px rgba(0,0,0,0.18);
  }

  /* Front */
  .card-front {
    left: 90px; top: 80px;
    background: radial-gradient(ellipse at 40% 45%, var(--maroon-light) 0%, var(--maroon) 45%, var(--maroon-deep) 100%);
  }
  .front-ornament {
    position: absolute; right: 0; top: 0;
    width: 330px; height: 110px;
    background: radial-gradient(ellipse at 70% 30%, rgba(227,180,122,0.55) 0%, rgba(227,180,122,0.2) 55%, rgba(227,180,122,0) 80%);
  }
  .front-logo {
    position: absolute; left: 70px; top: 120px;
    width: 300px; height: 110px;
    display: flex; align-items: center; justify-content: center;
  }
  .front-logo .brand-name {
    font-family: "Cinzel", serif; font-weight: 600;
    font-size: 30px; letter-spacing: 1px; color: var(--gold-soft);
  }
  .front-web {
    position: absolute; left: 0; right: 0; bottom: 50px;
    text-align: center;
    font-family: "Libre Baskerville", serif; font-weight: 700;
    font-size: 17px; color: var(--white); letter-spacing: 0.5px;
  }

  /* Back */
  .card-back {
    left: 490px; top: 500px;
    background: var(--white);
  }
  .back-logo {
    position: absolute; left: 40px; top: 34px;
    display: flex; align-items: center; gap: 10px;
  }
  .back-logo .mark {
    width: 14px; height: 14px; border-radius: 50%; background: var(--maroon);
  }
  .back-logo .brand-name {
    font-family: "Cinzel", serif; font-weight: 600;
    font-size: 24px; color: var(--maroon);
  }
  .back-title {
    position: absolute; right: 44px; top: 64px;
    font-size: 22px; color: var(--maroon);
  }
  .contact-list {
    position: absolute; left: 40px; top: 146px;
    list-style: none;
  }
  .contact-list li {
    display: flex; align-items: center; gap: 8px;
    font-size: 17px; color: var(--ink); line-height: 22px;
  }
  .contact-list svg, .address svg { width: 14px; height: 14px; fill: var(--maroon); flex: none; }
  .address {
    position: absolute; left: 388px; top: 188px;
    display: flex; gap: 8px;
    font-size: 17px; color: var(--ink); line-height: 22px;
  }
  .address svg { margin-top: 3px; }
  .back-bands { position: absolute; left: 0; bottom: 0; width: 620px; height: 120px; }
</style>
</head>
<body>

<section class="card card-front" aria-label="Card front">
  <div class="front-ornament" role="img" aria-label="Gold floral flourish ornament"></div>
  <div class="front-logo"><span class="brand-name">Marlow &amp; Quince</span></div>
  <p class="front-web">www.marlowquince.com</p>
</section>

<section class="card card-back" aria-label="Card back">
  <div class="back-logo"><span class="mark"></span><span class="brand-name">Marlow &amp; Quince</span></div>
  <h2 class="back-title" style="font-weight:400">Marlow &amp; Quince</h2>

  <ul class="contact-list">
    <li><svg viewBox="0 0 24 24"><path d="M6.6 10.8a15 15 0 0 0 6.6 6.6l2.2-2.2a1 1 0 0 1 1-.25 11.4 11.4 0 0 0 3.6.6 1 1 0 0 1 1 1V20a1 1 0 0 1-1 1A17 17 0 0 1 3 4a1 1 0 0 1 1-1h3.5a1 1 0 0 1 1 1 11.4 11.4 0 0 0 .6 3.6 1 1 0 0 1-.25 1z"/></svg>415-220-3140</li>
    <li><svg viewBox="0 0 24 24"><path d="M6 3h9l3 3v4H6zM3 11h18v8H3zM7 14h2v2H7zm4 0h6v2h-6z"/></svg>415-220-3141</li>
    <li><svg viewBox="0 0 24 24"><path d="M2 5h20v14H2zm2 2v.5l8 5.5 8-5.5V7z"/></svg>hello@marlowquince.com</li>
    <li><svg viewBox="0 0 24 24"><circle cx="12" cy="12" r="10"/></svg>www.marlowquince.com</li>
  </ul>

  <div class="address">
    <svg viewBox="0 0 24 24"><path d="M12 3 2 12h3v9h5v-6h4v6h5v-9h3z"/></svg>
    <p>4180 Linden Vale Rd.<br>Suite 210-118<br>Ashford, OR 97402</p>
  </div>

  <svg class="back-bands" viewBox="0 0 620 120" preserveAspectRatio="none" aria-hidden="true">
    <path d="M0 20 C160 40 380 60 620 58 L620 120 L0 120 Z" fill="var(--gold)"/>
    <path d="M0 40 C200 52 420 70 620 64 L620 120 L0 120 Z" fill="var(--cream)"/>
    <path d="M0 66 C220 70 420 86 620 74 L620 120 L0 120 Z" fill="var(--maroon)"/>
    <path d="M180 100 C340 92 480 88 620 84 L620 120 L160 120 Z" fill="var(--maroon-deep)"/>
  </svg>
</section>

</body>
</html>
```